Buch-/eBook-Cover für Sachbuch gesucht
Zielgruppe
We're selfpublishing nonfiction books. Interested are adults - mostly man (age range: 25-50) - who want to learn more about leadership at their workplaces.
Aufgabenstellung
The design should be clean and simple, title easy to read, good color contrast (the cover has to stand out from an white background).

```html
<!DOCTYPE html>
<html lang="en">
<head>
<meta charset="utf-8">
<title>Leadership – Book Cover</title>
<link rel="stylesheet" href="https://fonts.googleapis.com/css2?family=Roboto+Condensed:wght@600;700;800&display=swap">
<style>
  :root {
    --page-bg: #e9e9ea;
    --ink-dark: #1c2431;
    --deep-red: #b8301f;
    --flame: #e0542b;
    --orange: #ec8a36;
    --gold: #f0c35a;
    --sand: #d9c9a0;
    --teal: #2f8e90;
    --aqua: #63cdc6;
    --deep-teal: #173c47;
    --type: #f4f2ef;
  }
  * { margin: 0; padding: 0; box-sizing: border-box; }
  html, body {
    width: 1200px; height: 1200px; overflow: hidden;
    background: var(--page-bg);
  }
  .canvas {
    width: 1200px; height: 1200px;
    display: flex; align-items: center; justify-content: center;
  }
  .book-cover {
    position: relative;
    width: 780px; height: 1100px;
    overflow: hidden;
    font-family: "Roboto Condensed", "Arial Narrow", sans-serif;
    color: var(--type);
    background:
      radial-gradient(ellipse 60% 45% at 100% 30%, rgba(236,110,40,0.9), transparent 70%),
      radial-gradient(ellipse 55% 35% at 100% 55%, rgba(240,195,90,0.95), transparent 75%),
      radial-gradient(ellipse 60% 30% at 95% 92%, rgba(99,205,198,0.95), transparent 75%),
      radial-gradient(ellipse 55% 30% at 50% 47%, rgba(224,84,43,0.85), transparent 75%),
      radial-gradient(ellipse 60% 35% at 85% 72%, rgba(217,201,160,0.85), transparent 75%),
      linear-gradient(180deg, var(--ink-dark) 0%, #3a2226 12%, var(--deep-red) 28%, #a45a45 48%, #6f7a72 62%, var(--teal) 78%, var(--deep-teal) 100%);
  }
  .book-cover::before {
    content: ""; position: absolute; inset: 0;
    background: linear-gradient(90deg, rgba(20,28,40,0.55) 0%, rgba(20,28,40,0.2) 35%, transparent 60%);
  }
  .spine-crease {
    position: absolute; top: 0; bottom: 0; left: 36px; width: 2px;
    background: rgba(0,0,0,0.25);
    box-shadow: 1px 0 0 rgba(255,255,255,0.08);
  }
  .book-title,
  .book-subtitle,
  .author-name {
    position: absolute; left: 0; right: 0;
    text-align: center; padding-left: 42px;
    white-space: nowrap; line-height: 1;
  }
  .book-title {
    top: 245px;
    font-weight: 800; font-size: 150px;
    text-shadow: 0 4px 14px rgba(0,0,0,0.25);
  }
  .book-title span {
    display: inline-block;
    transform: scaleX(0.87);
    transform-origin: center;
  }
  .book-subtitle {
    top: 401px;
    font-weight: 700; font-size: 31px;
    letter-spacing: 0.2px;
  }
  .author-name {
    top: 1022px;
    font-weight: 700; font-size: 24px;
    letter-spacing: 0.3px;
  }
</style>
</head>
<body>
  <main class="canvas">
    <section class="book-cover">
      <div class="spine-crease"></div>
      <h1 class="book-title"><span>LEADERSHIP</span></h1>
      <p class="book-subtitle">FOSTERING GROWTH AND INSPIRING EXCELLENCE</p>
      <p class="author-name">DANIEL HARLOW</p>
    </section>
  </main>
</body>
</html>
```